Landscape design build company door flyer

I would like this flyer to convey a high-level of professionalism for a company that is excellent with communication with their clients as well as a company that does incredible installations

Went on vacation/holiday

```html
<!DOCTYPE html>
<html lang="en">
<head>
<meta charset="UTF-8">
<title>Cedar Ridge Builders – Outdoor Living Flyer</title>
<link href="https://fonts.googleapis.com/css2?family=Montserrat:wght@300;400;500;600;700;800&display=swap" rel="stylesheet">
<style>
  :root {
    --navy: #0e2b43;
    --navy-deep: #0b2438;
    --gold: #f5ad1a;
    --white: #ffffff;
    --paper-grey: #f1f1f1;
    --stage: #e6e6e6;
  }
  * { box-sizing: border-box; margin: 0; padding: 0; }
  html, body { width: 1200px; height: 1029px; overflow: hidden; }
  body {
    background: var(--stage);
    font-family: "Montserrat", sans-serif;
    position: relative;
  }
  .flyer {
    position: absolute;
    left: 220px; top: 25px;
    width: 760px; height: 978px;
    background: var(--white);
    overflow: hidden;
    box-shadow: 0 18px 40px rgba(0,0,0,0.25);
  }
  .hero {
    position: absolute; left: 0; top: 49px;
    width: 760px; height: 638px;
    background: var(--navy);
  }
  .logo-tab { position: absolute; left: 0; top: 0; width: 760px; height: 140px; }
  .brand {
    position: absolute; left: 284px; top: 30px; width: 182px;
    text-align: center; color: var(--navy);
  }
  .brand-mark {
    width: 48px; height: 48px; border-radius: 50%;
    background: var(--navy); margin: 0 auto 18px;
  }
  .brand-name { font-size: 12.5px; font-weight: 700; line-height: 1; white-space: nowrap; }
  .brand-tag { font-size: 7px; font-weight: 600; margin-top: 3px; white-space: nowrap; }
  .headline {
    position: absolute; left: 0; top: 114px; width: 760px;
    text-align: center; font-weight: 800; text-transform: uppercase;
    font-size: 44px; line-height: 46px; color: var(--white);
  }
  .headline .accent { color: var(--gold); display: block; }
  .about-title {
    position: absolute; left: 59px; top: 290px;
    color: var(--white); font-size: 18px; font-weight: 600; line-height: 1;
  }
  .about-copy {
    position: absolute; left: 59px; top: 318px; width: 264px;
    color: var(--white); font-size: 11.9px; line-height: 14.3px;
    text-align: justify; hyphens: auto;
  }
  .about-copy p + p { margin-top: 14.3px; }
  .photo { position: absolute; }
  .services {
    position: absolute; left: 0; top: 687px; width: 760px; height: 169px;
    background: linear-gradient(90deg, #fff 0%, #fff 52%, #d9dcdf 68%, #7f8b96 84%, #2b3e50 100%);
  }
  .services-title {
    position: absolute; left: 59px; top: 10px;
    font-size: 18px; font-weight: 700; color: var(--navy);
  }
  .service {
    position: absolute; display: flex; align-items: center; gap: 10px;
    font-size: 11.4px; font-weight: 700; color: var(--navy); white-space: nowrap;
  }
  .service svg { width: 26px; height: 26px; flex: none; }
  .seal { position: absolute; left: 587px; top: 33px; width: 114px; height: 114px; }
  .contact {
    position: absolute; left: 0; top: 856px; width: 760px; height: 115px;
    background: var(--navy-deep);
  }
  .contact-title {
    position: absolute; left: 59px; top: 16px;
    color: var(--white); font-size: 15px; font-weight: 600;
  }
  .phone {
    position: absolute; left: 58px; top: 36px;
    display: flex; align-items: center; gap: 14px;
    color: var(--gold); font-size: 41px; font-weight: 600; letter-spacing: -0.5px;
  }
  .phone svg { width: 36px; height: 36px; }
  .email {
    position: absolute; right: 30px; top: 50px;
    color: var(--white); font-size: 15px; font-weight: 300;
  }
</style>
</head>
<body>
<main class="flyer">
  <section class="hero">
    <div class="headline">Let’s Create<span class="accent">Your Dream Outdoor</span>Living Space!</div>

    <h2 class="about-title">ABOUT US</h2>
    <div class="about-copy">
      <p>Discover the endless possibilities for your outdoor space with The Cedar Ridge Builders Team. Our team of skilled artisans is dedicated to turning your outdoor space into a breathtaking oasis that you’ll love coming home to. Whether it’s a cozy patio for intimate gatherings, a sprawling deck to host memorable parties, or a custom paver driveway that adds instant curb appeal, our high-quality craftsmanship ensures stunning results that exceed your expectations.</p>
      <p>From concept to completion, we take pride in every detail, using the finest materials to withstand Seattle’s climate while adding timeless elegance to your property. Embrace the Pacific Northwest lifestyle and create cherished moments with family and friends in a captivating outdoor haven.</p>
    </div>

    <div class="photo" role="img" aria-label="Photo of a wooden deck with pergola and patio chairs" style="left:360px;top:299px;width:128px;height:127px;background:linear-gradient(180deg,#4f7a3a 0%,#7a6a4a 45%,#8a4a2c 100%);"></div>
    <div class="photo" role="img" aria-label="Photo of a covered outdoor kitchen with stone fireplace" style="left:498px;top:299px;width:203px;height:127px;background:linear-gradient(180deg,#8a5a34 0%,#5d5650 45%,#3f4850 100%);"></div>
    <div class="photo" role="img" aria-label="Photo of a modern home with a pool" style="left:360px;top:436px;width:128px;height:88px;background:linear-gradient(180deg,#d9dcd5 0%,#7fa88a 55%,#5fbdb5 100%);"></div>
    <div class="photo" role="img" aria-label="Photo of stone retaining wall steps" style="left:360px;top:534px;width:128px;height:88px;background:linear-gradient(180deg,#6a6a52 0%,#707478 40%,#4e5256 100%);"></div>
    <div class="photo" role="img" aria-label="Photo of a lakeside paver patio with firepit at dusk" style="left:498px;top:436px;width:203px;height:186px;background:linear-gradient(180deg,#3d6cb0 0%,#5b86c2 35%,#1f2e40 55%,#4f4a48 80%,#6b5d52 100%);"></div>
  </section>

  <svg class="logo-tab" viewBox="0 0 760 140" aria-hidden="true">
    <rect x="223" y="0" width="307" height="49" fill="#f1f1f1"/>
    <polygon points="223,49 284,133 466,133 530,49" fill="#ffffff"/>
    <rect x="284" y="0" width="182" height="133" fill="#ffffff"/>
  </svg>
  <div class="brand">
    <div class="brand-mark"></div>
    <div class="brand-name">CEDAR RIDGE BUILDERS</div>
    <div class="brand-tag">OUTDOOR LIVING SPACES</div>
  </div>

  <section class="services">
    <h2 class="services-title">OUR SERVICES</h2>

    <div class="service" style="left:62px;top:53px;">
      <svg viewBox="0 0 26 26"><path d="M3 11 L13 3 L23 11 V24 H3 Z" fill="none" stroke="#0e2b43" stroke-width="1.8"/><path d="M8 14h10M8 18h10M10 12v10M16 12v10" stroke="#0e2b43" stroke-width="1.3"/></svg>Paver Patios</div>
    <div class="service" style="left:62px;top:91px;">
      <svg viewBox="0 0 26 26"><path d="M3 11 L13 3 L23 11 V24 H3 Z" fill="none" stroke="#0e2b43" stroke-width="1.8"/><path d="M6 21 L10 15 H16 L20 21 Z" fill="#0e2b43"/></svg>Paver Driveways</div>
    <div class="service" style="left:62px;top:131px;">
      <svg viewBox="0 0 26 26"><path d="M3 11 L13 3 L23 11 V24 H3 Z" fill="none" stroke="#0e2b43" stroke-width="1.8"/><path d="M8 13h8v3h-5v3h6v3" fill="none" stroke="#0e2b43" stroke-width="2"/></svg>Retaining Walls</div>

    <div class="service" style="left:224px;top:53px;">
      <svg viewBox="0 0 26 26"><path d="M3 11 L13 3 L23 11 V24 H3 Z" fill="none" stroke="#0e2b43" stroke-width="1.8"/><path d="M10 10v9M15 10v9M10 13h5M7 20q2 -1.5 4 0t4 0t4 0" fill="none" stroke="#0e2b43" stroke-width="1.4"/></svg>Pools</div>
    <div class="service" style="left:224px;top:91px;">
      <svg viewBox="0 0 26 26"><path d="M3 11 L13 3 L23 11 V24 H3 Z" fill="none" stroke="#0e2b43" stroke-width="1.8"/><path d="M7 13h12v3H7zM8 16v6M18 16v6M11 16v6M15 16v6" fill="none" stroke="#0e2b43" stroke-width="1.3"/></svg>Decks &amp; Railings</div>
    <div class="service" style="left:224px;top:131px;">
      <svg viewBox="0 0 26 26"><path d="M3 11 L13 3 L23 11 V24 H3 Z" fill="none" stroke="#0e2b43" stroke-width="1.8"/><path d="M7 22 V16 L13 11 L19 16 V22 H15 V18 H11 V22 Z" fill="#0e2b43"/></svg>Firepits &amp; Fireplaces</div>

    <div class="service" style="left:391px;top:53px;">
      <svg viewBox="0 0 26 26"><path d="M3 11 L13 3 L23 11 V24 H3 Z" fill="none" stroke="#0e2b43" stroke-width="1.8"/><path d="M11 11h4v6h-4zM13 17v5M11 9h4" fill="none" stroke="#0e2b43" stroke-width="1.4"/></svg>Outdoor Lighting</div>
    <div class="service" style="left:391px;top:91px;">
      <svg viewBox="0 0 26 26"><path d="M3 11 L13 3 L23 11 V24 H3 Z" fill="none" stroke="#0e2b43" stroke-width="1.8"/><circle cx="13" cy="16.5" r="4.5" fill="none" stroke="#0e2b43" stroke-width="1.3"/><path d="M13 14v5M10.5 16.5h5" stroke="#0e2b43" stroke-width="1.3"/></svg>And More...</div>

    <svg class="seal" viewBox="0 0 114 114" role="img" aria-label="Experience seal">
      <defs>
        <radialGradient id="sealGold" cx="40%" cy="35%" r="70%">
          <stop offset="0%" stop-color="#f7e08a"/>
          <stop offset="55%" stop-color="#c9a12e"/>
          <stop offset="100%" stop-color="#7a5a10"/>
        </radialGradient>
      </defs>
      <circle cx="57" cy="57" r="56" fill="url(#sealGold)"/>
      <circle cx="57" cy="57" r="36" fill="#1a1a1a"/>
      <circle cx="57" cy="57" r="32" fill="url(#sealGold)" opacity="0.35"/>
    </svg>
  </section>

  <section class="contact">
    <h2 class="contact-title">CONTACT US TODAY</h2>
    <div class="phone">
      <svg viewBox="0 0 36 36" aria-hidden="true">
        <path d="M9 4 L14 4 L16 11 L12 14 Q15 21 22 24 L25 20 L32 22 L32 27 Q31 32 26 32 Q6 30 4 10 Q4 5 9 4 Z" fill="none" stroke="#f5ad1a" stroke-width="3.4" stroke-linejoin="round"/>
        <path d="M20 5 Q29 7 31 16M20 10 Q25 11 26 16" fill="none" stroke="#f5ad1a" stroke-width="2.4" stroke-linecap="round"/>
      </svg>
      <span>[206]-555-0148</span>
    </div>
    <div class="email">info@cedarridgebuilders.com</div>
  </section>
</main>
</body>
</html>
```